Innovation Company Business Card Design

I need to have my business card updated. The current card was designed when the company started 2.5 years ago and was a quick and dirty job.

I need a new card design that is more professional and has my updated company tag line.

I will include the old card's Corel Draw file, and EPS versions as examples of the current design. I will also include the company logo eps and corel version files.

The company pantone colour is pantone 1805 c (a dark red)

I want the design to convey the nature of our business as a strategic technology innovation company, but yet still be professional. We are funky vibey and work from an industrial style office in a vibey designer dominat part of town. Though are clients include large banks and corporate clients too.

The information that needs to be on the card is in attached word document (but doesn't have to be in this order or format)

Final version needs to be supplied in PNG preview, as well as PSD file format (or other editable file version) so that personal information on card can be easily edited and reprinted.

Target Market(s)

CEO's of small to medium size companies
Marketing Managers of large coporates
Account managers of Digital Agencies

Industry/Entity Type

Business

Requirements
Must have
• 86x54mm will be cut in rounded corner credit card size format (Except if you recommend otherwise in your design)
Nice to have
• Some kind of background transparency combined with the pantone colour that gives the card some dimension and depth. But no gradient fills please :-)
Should not have
• Basic gradient fills
• Clipart

```html
<!DOCTYPE html>
<html lang="en">
<head>
<meta charset="utf-8">
<title>Velterra Business Card</title>
<link href="https://fonts.googleapis.com/css2?family=Open+Sans:wght@400;600;700;800&display=swap" rel="stylesheet">
<style>
  :root {
    --brand-red: #bf301c;
    --brand-red-deep: #a01210;
    --brand-red-mid: #b32417;
    --paper: #ffffff;
    --edge: #d8d8d8;
    --band: rgba(255, 255, 255, 0.22);
  }
  * { margin: 0; padding: 0; box-sizing: border-box; }
  html, body {
    width: 1200px; height: 840px; overflow: hidden;
    background: var(--paper);
    font-family: "Open Sans", Arial, sans-serif;
  }
  .canvas { position: relative; width: 1200px; height: 840px; }

  .card {
    position: absolute; width: 572px; height: 360px;
    border-radius: 28px; overflow: hidden;
    box-shadow: 0 0 0 1px var(--edge), 2px 2px 3px rgba(0,0,0,0.18);
  }
  .card-front { left: 358px; top: 44px; background: var(--brand-red); }
  .card-back-left { left: 24px; top: 445px; background: var(--paper); }
  .card-back-right { left: 623px; top: 445px; background: var(--paper); }

  .card-art { position: absolute; inset: 0; }

  .wordmark {
    position: absolute; left: 0; width: 572px; top: 52px;
    text-align: center; color: var(--paper);
    font-weight: 800; font-size: 62px; letter-spacing: -1px; line-height: 1;
  }
  .tagline {
    position: absolute; right: 124px; top: 120px;
    color: var(--paper); font-size: 17px; font-weight: 400;
  }
  .name-band {
    position: absolute; left: 0; right: 0; top: 211px; height: 17px;
    background: var(--band);
  }
  .person {
    position: absolute; left: 0; width: 572px; top: 209px;
    text-align: center; color: var(--paper);
  }
  .person-name { font-size: 15px; font-weight: 700; line-height: 20px; letter-spacing: 0.3px; }
  .person-title { font-size: 7.5px; letter-spacing: 2.6px; line-height: 10px; }
  .contact {
    position: absolute; left: 0; width: 572px; top: 292px;
    text-align: center; color: var(--paper);
    font-size: 12.5px; line-height: 18px;
  }
  .contact .sep { margin: 0 5px; }

  .web-address {
    position: absolute; top: 312px;
    color: var(--brand-red);
    font-size: 9px; font-weight: 700; letter-spacing: 2.4px;
    white-space: nowrap;
  }
  .card-back-left .web-address { left: 206px; }
  .card-back-right .web-address { left: 205px; }
</style>
</head>
<body>
<main class="canvas">

  <section class="card card-front">
    <svg class="card-art" viewBox="0 0 572 360" aria-hidden="true">
      <rect x="0" y="0" width="200" height="360" fill="var(--brand-red-deep)"/>
      <rect x="200" y="0" width="120" height="360" fill="var(--brand-red-mid)"/>
    </svg>
    <div class="wordmark">Velterra</div>
    <div class="tagline">Strategic Innovation</div>
    <div class="name-band"></div>
    <div class="person">
      <div class="person-name">Daniel Marsh</div>
      <div class="person-title">FOUNDER &amp; MD</div>
    </div>
    <div class="contact">
      <div>daniel@velterra.com<span class="sep">•</span>0824417732<span class="sep">•</span>Velterra (Pty) Ltd</div>
      <div>Suite 204, 18 Ridgeview Rd<span class="sep">•</span>Parkhurst, JHB, RSA<span class="sep">•</span>010 482 3306</div>
    </div>
  </section>

  <section class="card card-back-left">
    <svg class="card-art" viewBox="0 0 572 360" aria-hidden="true">
      <polygon points="165,0 572,0 572,360 390,360" fill="var(--brand-red)"/>
    </svg>
    <div class="web-address">WWW.VELTERRA.COM</div>
  </section>

  <section class="card card-back-right">
    <svg class="card-art" viewBox="0 0 572 360" aria-hidden="true">
      <polygon points="0,0 165,0 110,360 0,360" fill="var(--brand-red)"/>
    </svg>
    <div class="web-address">WWW.VELTERRA.COM</div>
  </section>

</main>
</body>
</html>
```